Fitness Equipment & Service

I want to make the card eye catching and fun. We are called Corvane Motion Limited and we are based in Wales. We sell, install and service all types of fitness equipment from Skipping ropes, right through the Dumbbells, Kettle bells and Barbells through to state of the art Treadmills, Running Machines and Strength Equipment. We also design and install changing room furniture and lockers.

TYPOGRAPHY
We would like to use Futrura. Futura has an appearance of efficiency and forwardness. The typeface is derived
from simple geometric forms (near-perfect circles, triangles and squares) and is based on strokes of
near-even weight, which are low in contrast. This is most visible in the almost perfectly round stroke of
the o, which is nonetheless slightly ovoid.
The lowercase has tall ascenders, which rise above the cap line. The uppercase
characters present proportions similar to those of classical Roman capitals.

TYPOGRAPHIC CONSIDERATIONS
No Strike though
No Horizontal Scaling
No Drop Shadows
No Effects
Never use less than 120% Leading

OUR CORPORATE COLOURS
BRAND GUIDELINES
We were thinking that our primary colour palette consists of the Acid Green (Pantone 382) and Process Black.

We work closely with tquarly Ltd and would like to include their name on the card somewhere. I have attached images of the other brands that we work with as an idea or the small icons I have included that illustrate what we do?. I have very kindly been given permission to use any of the images off the files that I have included below, so I hope these help. I will include these below. I would be open to suggestions if it made the card more striking Can you do it?
Updates

Hi All, Just wanted to add a few thoughts but you are the guys with the creative visions (thats why are here) We are based in Wales, UK and we would be open to lots of different ideas on a theme but must be eye catching, Bold and FUN. If you can or think that the Welsh or any dragon could be put in there then go for it (its not a must have) We have also added some ideas for colour but again its over to you!! GO FOR IT ! Thanks and look forward to your visions! Owen

Hi All, Just thought I would sen through the contact details that need to be on the card. (if you want to play around with icons instead of the wording twitter, Facebook, go for it): Corvane Motion Limited Owen Pritchard Managing Director Mob: +44 (0)7582 913 406 e-mail: sales@corvanemotion.co.uk Web: Corvanemotion.co.uk twitter: @motionLetterbin Facebook: Corvane Motion Limited

```html
<!DOCTYPE html>
<html lang="en">
<head>
<meta charset="utf-8">
<title>Corvane Motion Limited – Business Card</title>
<link rel="stylesheet" href="https://fonts.googleapis.com/css2?family=Open+Sans:wght@400;600;700&display=swap">
<style>
  :root {
    --brand-blue: #26457f;
    --brand-navy: #141b3d;
    --paper: #ffffff;
    --backdrop: #e9e9eb;
    --ink-light: #ffffff;
  }
  html, body {
    margin: 0;
    padding: 0;
    width: 1189px;
    height: 1200px;
    overflow: hidden;
    background: var(--backdrop);
    font-family: "Open Sans", Arial, sans-serif;
  }
  .card {
    position: absolute;
    left: 140px;
    width: 917px;
    height: 524px;
    background: var(--paper);
    overflow: hidden;
    box-shadow: 0 2px 6px rgba(0,0,0,0.18);
  }
  .card--front { top: 45px; }
  .card--back { top: 623px; }

  .card__wave {
    position: absolute;
    inset: 0;
    width: 917px;
    height: 524px;
  }

  .brand-mark {
    position: absolute;
    border-radius: 50%;
    background: var(--brand-blue);
  }
  .brand-name {
    position: absolute;
    margin: 0;
    color: var(--brand-navy);
    font-weight: 700;
    line-height: 1.2;
    letter-spacing: 0.02em;
  }

  .card--front .brand-mark { left: 97px; top: 42px; width: 166px; height: 166px; }
  .card--front .brand-name { left: 62px; top: 246px; width: 250px; font-size: 26px; text-align: center; }

  .card--back .brand-mark { left: 296px; top: 54px; width: 278px; height: 278px; }
  .card--back .brand-name { left: 0; top: 384px; width: 917px; font-size: 44px; text-align: center; }

  .person {
    position: absolute;
    right: 47px;
    top: 226px;
    text-align: right;
    color: var(--ink-light);
  }
  .person__name {
    margin: 0;
    font-size: 40px;
    font-weight: 700;
    line-height: 1.2;
  }
  .person__role {
    margin: 0;
    font-size: 27px;
    font-weight: 400;
    line-height: 1.2;
  }

  .contact-list, .social-list {
    position: absolute;
    margin: 0;
    padding: 0;
    list-style: none;
    color: var(--ink-light);
    font-size: 25px;
    line-height: 1.2;
  }
  .contact-list { right: 35px; top: 378px; }
  .social-list { left: 33px; top: 418px; }
  .contact-list li, .social-list li {
    display: flex;
    align-items: center;
    height: 40px;
  }
  .contact-list li { justify-content: flex-end; }
  .contact-icon { width: 21px; height: 21px; margin-left: 19px; flex: none; }
  .social-icon {
    width: 20px; height: 20px;
    margin-right: 18px;
    background: var(--ink-light);
    flex: none;
  }
</style>
</head>
<body>

<section class="card card--front">
  <svg class="card__wave" viewBox="0 0 917 524" aria-hidden="true">
    <path fill="#26457f" d="M0,376 C250,324 400,284 520,209 C650,129 760,102 917,102 L917,524 L0,524 Z"/>
    <path fill="none" stroke="#ffffff" stroke-width="4" d="M0,385 C250,333 400,293 520,218 C650,138 760,111 917,111"/>
  </svg>

  <div class="brand-mark"></div>
  <p class="brand-name">Corvane Motion Limited</p>

  <div class="person">
    <p class="person__name">Owen Pritchard</p>
    <p class="person__role">Managing Director</p>
  </div>

  <ul class="contact-list">
    <li>+44 (0)7582 913 406
      <svg class="contact-icon" viewBox="0 0 21 21" aria-label="Phone"><rect width="21" height="21" fill="#fff"/><rect x="6.5" y="3" width="8" height="15" rx="1.5" fill="#26457f"/><rect x="8" y="5" width="5" height="5" fill="#fff"/></svg>
    </li>
    <li>sales@corvanemotion.co.uk
      <svg class="contact-icon" viewBox="0 0 21 21" aria-label="Email"><rect width="21" height="21" fill="#fff"/><rect x="3" y="5" width="15" height="11" fill="#26457f"/><path d="M3.5,5.5 L10.5,11.5 L17.5,5.5" fill="none" stroke="#fff" stroke-width="1.4"/></svg>
    </li>
    <li>Corvanemotion.co.uk
      <svg class="contact-icon" viewBox="0 0 21 21" aria-label="Website"><rect width="21" height="21" fill="#fff"/><circle cx="10.5" cy="10.5" r="7" fill="#26457f"/><path d="M3.5,10.5 H17.5 M10.5,3.5 V17.5" stroke="#fff" stroke-width="1.2"/></svg>
    </li>
  </ul>

  <ul class="social-list">
    <li><span class="social-icon"></span>@motionLetterbin</li>
    <li><span class="social-icon"></span>Corvane Motion Limited</li>
  </ul>
</section>

<section class="card card--back">
  <div class="brand-mark"></div>
  <p class="brand-name">Corvane Motion Limited</p>
</section>

</body>
</html>
```